Dentistry

Dentist's personal business card. No logo needed. The card shoul deliver the massage of reliability, professionalism, experience.
Please ad the full brief of the project: down the line it says: the winning look should be precise and pristine NO pictures of Teeth, smiles, instruments etc.

The details to be desplaid are:
Dr. Rob Tavolen
Doctor of Dental Surgery
PHD
Web. Www.drtavolen.com
Email. Rob@drtavolen.com
Tel 07742318590
Surgery address. 27Bferndale road London SW4 8QT UK
62 Wexley Row London SW3 2HN. Uk

Reason: Decided to make the payment unrefundable in order to get more designers involved.

Requirements
Should not have
• Logo, teeth, smile any sort of instruments.

```html
<!DOCTYPE html>
<html lang="en">
<head>
<meta charset="utf-8">
<title>Dr. Rob Tavolen – Business Card</title>
<link rel="stylesheet" href="https://fonts.googleapis.com/css2?family=Open+Sans:wght@300;400;600&display=swap">
<style>
  :root {
    --card-bg: #f2f2f2;
    --ink-strong: #555555;
    --ink-soft: #5c5c5c;
    --rule: #8a8a8a;
  }
  html, body {
    margin: 0;
    padding: 0;
    width: 1200px;
    height: 699px;
    overflow: hidden;
    background: var(--card-bg);
  }
  .card {
    position: relative;
    width: 1200px;
    height: 699px;
    background: radial-gradient(ellipse at 50% 40%, #f5f5f5 0%, var(--card-bg) 70%);
    font-family: "Open Sans", sans-serif;
    color: var(--ink-soft);
  }
  .identity {
    position: absolute;
    left: 0;
    right: 0;
    top: 94px;
    text-align: center;
    padding-left: 12px;
  }
  .identity__name {
    margin: 0;
    font-weight: 600;
    font-size: 42px;
    line-height: 58px;
    color: var(--ink-strong);
  }
  .identity__rule {
    display: block;
    width: 375px;
    height: 2px;
    margin: 12px auto 0;
    background: linear-gradient(90deg, rgba(120,120,120,0) 0%, #7a7a7a 50%, rgba(120,120,120,0) 100%);
  }
  .identity__title {
    margin: 4px 0 0;
    font-weight: 300;
    font-size: 34px;
    line-height: 48px;
    color: var(--ink-soft);
  }
  .contact {
    position: absolute;
    left: 0;
    right: 0;
    top: 399px;
    text-align: center;
    padding-left: 6px;
    font-weight: 300;
    font-size: 23px;
    line-height: 31px;
    color: var(--ink-soft);
  }
  .contact p { margin: 0; }
  .contact__label {
    font-weight: 600;
    color: var(--ink-strong);
  }
  .web-band {
    position: absolute;
    left: 0;
    right: 0;
    top: 583px;
    height: 34px;
  }
  .web-band__rule {
    position: absolute;
    top: 17px;
    height: 1px;
    background: var(--rule);
  }
  .web-band__rule--left { left: 0; width: 116px; }
  .web-band__rule--right { left: 409px; right: 0; }
  .web-band__url {
    position: absolute;
    left: 151px;
    top: 0;
    font-weight: 300;
    font-size: 25px;
    line-height: 34px;
    color: var(--ink-strong);
  }
</style>
</head>
<body>
  <main class="card">
    <header class="identity">
      <h1 class="identity__name">Dr. Rob Tavolen</h1>
      <span class="identity__rule"></span>
      <p class="identity__title">Doctor of Dental Surgery<br>PHD</p>
    </header>

    <section class="contact">
      <p><span class="contact__label">Address:</span> 27Bferndale road London SW4<br>8QT UK 62 Wexley Row London SW3 2HN. Uk</p>
      <p><span class="contact__label">Ph:</span> 07742318590</p>
      <p><span class="contact__label">Email:</span> Rob@drtavolen.com</p>
    </section>

    <footer class="web-band">
      <span class="web-band__rule web-band__rule--left"></span>
      <span class="web-band__url">www.drtavolen.com</span>
      <span class="web-band__rule web-band__rule--right"></span>
    </footer>
  </main>
</body>
</html>
```